Etiketten für Bio Seifen
Zielgruppe
Wir stellen hochwertig 'handgemachte' Bio-Seifen her. Die Zielgruppe ist von 3-99 Jahren und zusätzlich haben wir auch noch Seife für Hunde.
Der Firmenname ist 'Verdolina'
Aufgabenstellung
Das Etikett soll Bezug auf Natur, Bio, Nachhaltigkeit nehmen. Wir stellen uns 'weiche' Aquarellfarben vor...Seife: Lavendel, Calendular, 7 Kräuter etc.
Das Etikett soll auf eine Beutelschachtel. Die Schachtel hat eine Anmaße: Breite 55mm; Höhe 120mm; Tiefe 30mm
Das Etikett soll im vorderen- und hinteren Bereich zusammenhängend geklebt werden.
Das Etikett soll eine Abmaße von: Breite 51mm; Höhe 114mm haben (Vorderseite) Rückseite gleich.
Wir möchten die Produkte auch gerne nummerieren, d.h. jede Seife hat eine Nummer die nicht zu groß dargestellt werden soll aber trotzdem gut leserlich.
Wir haben noch ein paar Bilder hochgeladen wie wir uns das ungefähr vorstellen.

```html
<!DOCTYPE html>
<html lang="de">
<head>
<meta charset="utf-8">
<title>Verdolina – Seifenetikett</title>
<link rel="stylesheet" href="https://fonts.googleapis.com/css2?family=Allura&family=Montserrat:wght@400&display=swap">
<style>
  :root {
    --paper: #ffffff;
    --label-base: #f8f6f3;
    --lilac: #b7a3c9;
    --lilac-deep: #9b84b3;
    --sage: #8fb3a6;
    --leaf: #5f8f7e;
    --lavender: #7a5aa8;
    --blossom: #efc1c4;
    --badge-text: #ffffff;
  }
  * { margin: 0; padding: 0; box-sizing: border-box; }
  html, body {
    width: 1200px;
    height: 582px;
    overflow: hidden;
    background: var(--paper);
  }
  .canvas {
    position: relative;
    width: 1200px;
    height: 582px;
    background: var(--paper);
  }
  .wordmark {
    position: absolute;
    top: 40px;
    left: 0;
    width: 100%;
    text-align: center;
    font-family: "Allura", cursive;
    font-weight: 400;
    font-size: 128px;
    line-height: 1;
    color: var(--lilac);
  }
  .label {
    position: absolute;
    left: 290px;
    top: 262px;
    width: 620px;
    height: 272px;
    background: var(--label-base);
    overflow: hidden;
  }
  .label-botanicals {
    position: absolute;
    inset: 0;
    background:
      radial-gradient(ellipse 22% 55% at 12% 60%, rgba(95,143,126,0.55), transparent 70%),
      radial-gradient(ellipse 22% 55% at 88% 60%, rgba(95,143,126,0.55), transparent 70%),
      radial-gradient(ellipse 10% 35% at 28% 72%, rgba(122,90,168,0.55), transparent 70%),
      radial-gradient(ellipse 10% 35% at 72% 72%, rgba(122,90,168,0.55), transparent 70%),
      radial-gradient(ellipse 30% 20% at 50% 8%, rgba(143,179,166,0.35), transparent 70%),
      radial-gradient(ellipse 8% 10% at 50% 90%, rgba(239,193,196,0.6), transparent 70%),
      var(--label-base);
  }
  .badge {
    position: absolute;
    left: 183px;
    top: 74px;
    width: 254px;
    height: 136px;
  }
  .badge svg { position: absolute; inset: 0; }
  .badge-number {
    position: absolute;
    left: 50%;
    top: -16px;
    transform: translateX(-50%);
    width: 36px;
    height: 36px;
    border-radius: 50%;
    background: var(--lilac);
    border: 3px solid var(--label-base);
    box-shadow: 0 0 0 2px var(--lilac);
    color: var(--badge-text);
    font-family: "Montserrat", sans-serif;
    font-size: 15px;
    line-height: 30px;
    text-align: center;
  }
  .badge-name {
    position: absolute;
    top: 22px;
    width: 100%;
    text-align: center;
    font-family: "Allura", cursive;
    font-size: 60px;
    line-height: 1;
    color: var(--badge-text);
  }
  .badge-tagline {
    position: absolute;
    top: 102px;
    left: 26px;
    right: 26px;
    display: flex;
    align-items: center;
    gap: 8px;
    font-family: "Montserrat", sans-serif;
    font-size: 11px;
    letter-spacing: 0.5px;
    color: var(--badge-text);
  }
  .badge-tagline::before,
  .badge-tagline::after {
    content: "";
    flex: 1;
    height: 1px;
    background: var(--badge-text);
  }
</style>
</head>
<body>
<main class="canvas">
  <h1 class="wordmark">Verdolina</h1>

  <section class="label">
    <div class="label-botanicals" role="img" aria-label="Aquarell-Botanik: Eukalyptuszweige, Lavendelblüten, grüne Blätter und zarte rosa Blüten"></div>

    <div class="badge">
      <svg viewBox="0 0 254 136" width="254" height="136" aria-hidden="true">
        <rect x="2" y="2" width="250" height="132" rx="34" fill="var(--lilac)" stroke="var(--lilac-deep)" stroke-width="0"/>
        <rect x="8" y="8" width="238" height="120" rx="30" fill="none" stroke="#ffffff" stroke-width="1.5" opacity="0.9"/>
      </svg>
      <div class="badge-number">1.</div>
      <div class="badge-name">Verdolina</div>
      <div class="badge-tagline">HANDMADE</div>
    </div>
  </section>
</main>
</body>
</html>
```